The 22 Rules and Traps of House Lending or the 22 things that will derail your transaction and how to prevent them.

I am looking to do a series of 4 to 5 e-books that should have a consistent format and theme

The first of these should be entitled, "The 22 Rules and Traps of House Lending" That is similar in style to the attached e-book.
The attached e-book is pretty much the style that I am looking for, The same format can be followed. I have attached a black and white head shot image for the head shot areas that appears on page two of the attached e-book. I have also attached my company logo.
Please feel free to use the same or similar colors in my logo for the lay-out of the e-book. However please do not feel limited to those colors. - Feel free to use your imagination.

The content can be found here.

http://www.fredtheloanfox.example/loan-advice.php

For the final “About” page of the e-book - Please entitle it… About Fred the Loan Fox.
The content for the last page can be found in the attached document - Owen Thistlewood bio2

The first page is where the creativity come in

Requirements
Must have
• Note that this project is for one e-book - However, once the designer and format is chosen the remainder of the projects will be launched

```html
<!DOCTYPE html>
<html lang="en">
<head>
<meta charset="utf-8">
<title>The 22 Rules and Traps of House Lending – Page 3</title>
<link rel="stylesheet" href="https://fonts.googleapis.com/css2?family=Jost:wght@400;500;700;800&family=Libre+Baskerville:wght@700&display=swap">
<style>
  :root{
    --navy:#1f3a6e;
    --badge:#27539c;
    --accent-red:#e3231c;
    --accent-blue:#2f5cae;
    --body:#4a4a4a;
    --paper:#ffffff;
  }
  *{box-sizing:border-box;margin:0;padding:0}
  html,body{width:900px;height:1200px;overflow:hidden;background:var(--paper)}
  .page{position:relative;width:900px;height:1200px;font-family:"Jost",sans-serif;color:var(--body)}
  .tip{position:absolute;left:63px;width:770px}
  .tip-number{position:absolute;left:-42px;top:-4px;width:48px;height:48px;border-radius:50%;
    background:var(--badge);color:#fff;font-family:"Libre Baskerville",serif;font-weight:700;
    font-size:23px;display:flex;align-items:center;justify-content:center;padding-bottom:4px}
  .tip-title{font-family:"Jost",sans-serif;font-weight:500;font-size:28.5px;line-height:1.2;color:var(--navy);text-indent:44px;margin-bottom:18px}
  .tip-title .dont{color:var(--accent-red);font-weight:700}
  .tip-title .do{color:var(--accent-blue);font-weight:700}
  .tip-text{font-size:15px;line-height:1.45;margin-bottom:16px}
  .tip-callout{font-weight:800;font-size:17px;line-height:1.65;color:var(--accent-blue);margin-top:20px}
  .footer{position:absolute;left:63px;right:55px;top:1098px;height:40px;display:flex;align-items:center}
  .brand{display:flex;flex-direction:column;color:var(--navy);font-weight:700}
  .brand-name{font-size:22px;line-height:1}
  .brand-sub{font-size:8px;letter-spacing:.3px;margin-top:2px}
  .footer-rule{width:2px;height:38px;background:var(--navy);margin:0 12px}
  .footer-title,.footer-licence{font-family:"Libre Baskerville",serif;font-variant:small-caps;color:var(--navy);font-size:14px}
  .footer-title{width:320px}
  .footer-licence{margin-left:20px}
  .page-number{margin-left:auto;width:24px;height:26px;background:var(--navy);color:#fff;font-family:"Libre Baskerville",serif;font-size:15px;display:flex;align-items:center;justify-content:center}
</style>
</head>
<body>
<div class="page">

  <section class="tip" style="top:58px">
    <div class="tip-number">01</div>
    <h2 class="tip-title"><span class="dont">Don’t</span> apply for two mortgage at the same time for the same transaction.</h2>
    <p class="tip-text">Popular wisdom states that it is always best to “shop around” for the best terms for your mortgage. While this is true, once you have decided upon an acceptable lender with acceptable terms, this is where your shopping should end. If you have two mortgage brokers working on your loan simultaneously it can adversely effect your credit and the underwriting process. If a particular lender learns that you are trying to obtain financing for a transaction they are working on you run the risk of the lender canceling your loan application.</p>
  </section>

  <section class="tip" style="top:276px">
    <div class="tip-number">02</div>
    <h2 class="tip-title"><span class="do">Do</span> let your agent or mortgage professional know if you are planning to travel while applying for a loan.</h2>
    <p class="tip-text">Going out of town during the process of securing home financing can create havoc with the closing of your loan. If you are planning to be out of town let both your real estate agent and mortgage professional know early enough so they can plan accordingly. Planning the closing of your loan transaction around your trip can be easily done if your agent and mortgage professional are aware of your travel plans.</p>
    <p class="tip-text">A good rule of thumb is to let them know three weeks in advance. Emergency trips do happen, and if you need to be out of town on an emergency basis please let your agent and mortgage professional know as soon as possible so appropriate planning can take place.</p>
    <p class="tip-callout">Please also provide a way that you can be contacted so if you are required to provide paperwork, or if paperwork needs to be sent to you, it can easily be done while you are out of town.</p>
  </section>

  <section class="tip" style="top:696px">
    <div class="tip-number">03</div>
    <h2 class="tip-title"><span class="do">Do</span> continue making your payments on your mortgages or other loans during the underwriting process.</h2>
    <p class="tip-text">This one may seem quite obvious but, some borrowers wrongly assume that if they are selling a home, refinancing a home mortgage, or paying off debt with a debt consolidation mortgage, those loans will soon be eliminated so the neces-sity to keep those payments going is also eliminated. Not keeping up on all of your payment could result in a late-payment penalty on your existing mortgage and/or a 30-day late on your credit.</p>
    <p class="tip-callout">It is very important to keep up on all payments during the loan process to keep any negative information from being reported to the credit agencies and poten-tially damaging your credit score.</p>
  </section>

  <footer class="footer">
    <div class="brand">
      <span class="brand-name">HarborLine</span>
      <span class="brand-sub">HARBORLINE HOME LOAN CO</span>
    </div>
    <div class="footer-rule"></div>
    <span class="footer-title">The 22 Rules and Traps of House Lending</span>
    <span class="footer-licence">Licence MLO#40782</span>
    <span class="page-number">3</span>
  </footer>

</div>
</body>
</html>
```